Aid, Development & Consulting Firm

Brantwell Fennimore Consulting Pty Ltd is a small firm in Australia whose principal works in the area of aid and development. His experience is broad ranging from aid project design and evaluation; to offering security advice in running aid operations in dangerous situations. He works with governments and private firms in conducting training for personnel travelling to work in dangerous or difficult regions. He has worked for many years with NGO's (aid organisations) and consults to the WCA. He works in locations all over the globe which include trouble spots like Iraq and Sudan, to sleepier locales like Samoa and Fiji. Being on Asia's doorstep much time is spent in Asia eg Indonesia, Vietnam. He is often called on to monitor and evaluate aid projects throughtout the globe.

Target Market(s)

Government Aid Divisions eg in Oz, PacRelief; WCA; NGO's and consulting firms who work in developing countries

Industry/Entity Type

Security

Requirements
Nice to have
• Try and incorporate a global feel without being obvious i.e. no starving children as the primary work done is a step beyond obvious aid relief. Something very simple but bold and stylish as card holder is not a "touchy" feely person
Should not have
• No starving kid type scenarios. Prefer no pictures

```html
<!DOCTYPE html>
<html lang="en">
<head>
<meta charset="utf-8">
<title>Brantwell Fennimore Consulting – Business Card</title>
<link href="https://fonts.googleapis.com/css2?family=Arimo:wght@400;700&family=Michroma&display=swap" rel="stylesheet">
<style>
  :root {
    --stage-light: #f4f4f5;
    --stage-edge: #dcdcde;
    --card-front: #000000;
    --card-back: #88898c;
    --back-disc: #6f7073;
    --accent-blue: #1a9ad6;
    --icon-blue: #1f4f8f;
    --text-white: #ffffff;
  }
  html, body {
    margin: 0;
    padding: 0;
    width: 1200px;
    height: 900px;
    overflow: hidden;
  }
  body {
    position: relative;
    background: radial-gradient(ellipse at center, var(--stage-light) 40%, var(--stage-edge) 100%);
    font-family: "Arimo", Arial, sans-serif;
  }
  .card {
    position: absolute;
    left: 281px;
    width: 637px;
    height: 388px;
    overflow: hidden;
    box-shadow: 0 2px 6px rgba(0,0,0,0.18);
  }
  .card-front { top: 54px; background: var(--card-front); }
  .card-back  { top: 473px; background: var(--card-back); }

  .front-disc {
    position: absolute;
    left: 360px;
    top: 128px;
    width: 300px;
    height: 300px;
    border-radius: 50%;
    background: radial-gradient(circle at 70% 70%, #4a4a4c 0%, #262627 55%, #0c0c0c 100%);
  }
  .brand-mark {
    position: absolute;
    left: 269px;
    top: 14px;
    width: 100px;
    height: 100px;
    border-radius: 50%;
    background: linear-gradient(180deg, #1595d3 0%, #bfe6f7 50%, #1595d3 100%);
  }
  .company-name {
    position: absolute;
    left: 0;
    right: 0;
    top: 118px;
    margin: 0;
    text-align: center;
    color: var(--text-white);
    font-weight: 700;
    font-size: 28px;
    letter-spacing: -0.2px;
  }
  .services {
    position: absolute;
    left: 0;
    right: 0;
    top: 163px;
    display: flex;
    justify-content: center;
    align-items: center;
    gap: 20px;
    color: var(--accent-blue);
    font-family: "Michroma", sans-serif;
    font-size: 12px;
    letter-spacing: 2px;
  }
  .services .divider {
    width: 1.5px;
    height: 20px;
    background: var(--accent-blue);
  }
  .holder {
    position: absolute;
    left: 0;
    right: 0;
    top: 238px;
    text-align: center;
    font-family: "Michroma", sans-serif;
  }
  .holder-name {
    margin: 0;
    color: var(--text-white);
    font-size: 21px;
    letter-spacing: 0.5px;
  }
  .holder-role {
    margin: 2px 0 0;
    color: var(--accent-blue);
    font-size: 15px;
    letter-spacing: 3px;
    font-variant: small-caps;
    text-transform: lowercase;
  }

  .back-disc {
    position: absolute;
    left: 354px;
    top: 125px;
    width: 312px;
    height: 312px;
    border-radius: 50%;
    background: var(--back-disc);
  }
  .contact {
    position: absolute;
    left: 52px;
    color: var(--text-white);
    font-size: 19px;
  }
  .contact-row {
    display: flex;
    align-items: center;
    height: 27.5px;
  }
  .contact-row svg {
    width: 24px;
    height: 24px;
    margin-right: 15px;
    flex: none;
    fill: var(--icon-blue);
  }
  .address { top: 126px; }
  .address .contact-row { align-items: flex-start; }
  .address p { margin: 0; line-height: 27.5px; }
  .lines { top: 237px; }
</style>
</head>
<body>

<section class="card card-front">
  <div class="front-disc"></div>
  <div class="brand-mark"></div>
  <h1 class="company-name">Brantwell Fennimore Consulting Pty Ltd</h1>
  <div class="services">
    <span>AID</span><span class="divider"></span>
    <span>CONFLICT</span><span class="divider"></span>
    <span>ANALYSIS</span><span class="divider"></span>
    <span>EVALUATION</span>
  </div>
  <div class="holder">
    <p class="holder-name">B. Brantwell Fennimore</p>
    <p class="holder-role">Director</p>
  </div>
</section>

<section class="card card-back">
  <div class="back-disc"></div>

  <div class="contact address">
    <div class="contact-row">
      <svg viewBox="0 0 24 24" aria-hidden="true"><path d="M12 1a8 8 0 0 0-8 8c0 5 8 14 8 14s8-9 8-14a8 8 0 0 0-8-8z"/></svg>
      <p>42 Harwood Street<br>Linden Park<br>SA 5065 Australia</p>
    </div>
  </div>

  <div class="contact lines">
    <div class="contact-row">
      <svg viewBox="0 0 24 24" aria-hidden="true"><path d="M2 9c0-3 4-5 10-5s10 2 10 5v2h-5V9H7v2H2z"/><path d="M6 12h12l2 8H4z"/></svg>
      <span>+61 8 5550 1847</span>
    </div>
    <div class="contact-row">
      <svg viewBox="0 0 24 24" aria-hidden="true"><path d="M7 1h10a2 2 0 0 1 2 2v18a2 2 0 0 1-2 2H7a2 2 0 0 1-2-2V3a2 2 0 0 1 2-2zm0 3v14h10V4zm5 15.5a1.2 1.2 0 1 0 0 2.4 1.2 1.2 0 0 0 0-2.4z"/></svg>
      <span>+61 (0) 400 555 162</span>
    </div>
    <div class="contact-row">
      <svg viewBox="0 0 24 24" aria-hidden="true"><path d="M1 5h22v14H1zm2 2v10h18V7zm0 0 9 7 9-7v2l-9 7-9-7z"/></svg>
      <span>brantwell@mailhub.com</span>
    </div>
    <div class="contact-row">
      <svg viewBox="0 0 24 24" aria-hidden="true"><path d="M1 5h22v14H1zm2 2v10h18V7zm0 0 9 7 9-7v2l-9 7-9-7z"/></svg>
      <span>brantwellf@inboxly.com</span>
    </div>
  </div>
</section>

</body>
</html>
```